Web Design Project for a beach town business owner who supports new families with their babies.

I'm looking for a basic website with the following pages: home, about, services, FAQs, blog, and contact page. I have images and content ready to go.

Target Market(s)

Men and women between the ages of 22 and 42, growing families

Industry/Entity Type

Postpartum Doula

Coding

Number of Pages Required

Font styles to use
Serif
Other font styles liked:
• My logo font is "Nexa Bold" - so coordinating fonts with that are ideal

Colors
00AB8E
00BBA5
67D7C9
C6EFE9
E9F9F6
EE7325
F08F49
F5BC92
FAE3D3
FDF4ED

Requirements
Must have
• Warm and professional vibe, multicultural images, aligned with my branding colors and font ("Nexa Bold"; COLORS: light blue hex: #2FCEC2 R: 47 G: 206 B: 194 dark blue hex: #007C7C R: 0 G: 124 B: 124 orange hex: #F77B4E R: 247 G: 123 B: 78), good SEO
Should not have
• Ultra feminine images, baby bottles, cutesy images.

```html
<!DOCTYPE html>
<html lang="en">
<head>
<meta charset="utf-8">
<title>Harborline Families Postpartum Care</title>
<link rel="stylesheet" href="https://fonts.googleapis.com/css2?family=Montserrat:wght@400;500;600&family=Arimo:ital,wght@0,400;0,700;1,400&display=swap">
<style>
  :root{
    --teal:#1aae95;
    --teal-deep:#00a389;
    --teal-bright:#1ab89f;
    --orange:#e8601f;
    --orange-soft:#f08f49;
    --ink:#222;
    --muted:#666;
    --footer:#1d1d1d;
    --white:#fff;
  }
  *{box-sizing:border-box;margin:0;padding:0}
  html,body{width:1200px;height:3903px;overflow:hidden;background:#fff}
  body{position:relative;font-family:"Arimo",Arial,sans-serif;color:var(--ink)}
  .abs{position:absolute}
  .heading{font-family:"Montserrat",Arial,sans-serif}

  /* header */
  .site-header{top:0;left:0;width:1200px;height:138px;background:#fff;z-index:2}
  .brand-badge{left:110px;top:18px;width:194px;height:194px;border-radius:50%;background:#fff;z-index:3;display:flex;align-items:center;justify-content:center;text-align:center;font-family:"Montserrat",sans-serif;font-weight:600;font-size:19px;line-height:1.25;color:var(--teal);box-shadow:0 2px 6px rgba(0,0,0,.08)}
  .main-nav{right:112px;top:64px;display:flex;gap:52px;font-family:"Montserrat",sans-serif;font-weight:500;font-size:14px;color:#333}
  .main-nav .active{color:var(--orange)}

  /* hero */
  .hero{top:138px;left:0;width:1200px;height:720px;background:linear-gradient(100deg,#5b7a3b 0%,#7a9a4d 35%,#3f6b3a 55%,#2a8dc4 80%,#1d7fb7 100%)}
  .hero-kicker{left:111px;top:415px;font-size:33px;color:#fff;font-weight:500}
  .hero-title{left:111px;top:462px;font-size:50px;color:#fff;font-weight:500}
  .btn{display:inline-block;font-family:"Montserrat",sans-serif;font-weight:500;font-size:15px;color:#fff;text-transform:uppercase;border-radius:3px}
  .btn-orange{background:var(--orange)}
  .btn-teal{background:var(--teal)}
  .hero-cta{left:111px;top:550px;width:194px;height:55px;line-height:55px;text-align:center}

  /* about */
  .about-title{left:115px;top:957px;font-size:38px;color:var(--teal);font-weight:500}
  .about-sub{left:115px;top:1012px;font-size:19px;color:var(--orange);font-weight:500}
  .about-copy{left:116px;top:1062px;width:452px;font-size:15px;line-height:26px;color:#444;text-align:justify}
  .about-copy p+p{margin-top:25px}
  .about-cta{left:116px;top:1348px;width:146px;height:52px;line-height:52px;text-align:center;font-size:16px}
  .about-photo{left:620px;top:970px;width:460px;height:462px;border-radius:50%;background:radial-gradient(circle at 40% 40%,#9fb88a,#6b5a44 60%,#4a3b2d);border-bottom:6px solid var(--teal)}

  /* key areas */
  .key-areas{top:1508px;left:0;width:1200px;height:554px;background:var(--orange)}
  .key-photo{left:0;top:0;width:650px;height:554px;background:linear-gradient(90deg,#8a8f98 0%,#b59a86 40%,#c99675 75%,var(--orange) 100%)}
  .key-title{left:615px;top:56px;font-size:36px;color:#fff;font-weight:500}
  .key-rule{left:615px;top:118px;width:60px;height:3px;background:#fff}
  .key-list{left:615px;top:148px;width:470px;list-style:none;color:#fff;font-size:13.5px;line-height:26px}
  .key-list li{position:relative;padding-left:40px;margin-bottom:22px}
  .key-list svg{position:absolute;left:0;top:8px}

  /* blog */
  .section-title{left:0;width:1200px;text-align:center;font-size:36px;font-weight:500}
  .blog-title{top:2118px;color:var(--teal)}
  .blog-title span{color:var(--orange)}
  .title-rule{left:575px;width:50px;height:3px}
  .feature-photo{left:111px;top:2229px;width:477px;height:309px;background:linear-gradient(120deg,#6d6258,#9a8577 50%,#5a4c44)}
  .feature-heading{left:111px;top:2562px;font-size:16.5px;font-weight:500;color:#222}
  .date{font-family:"Montserrat",sans-serif;font-size:16px;color:var(--orange);font-weight:500}
  .feature-date{left:111px;top:2592px}
  .feature-copy{left:111px;top:2630px;width:470px;font-size:13px;line-height:28px;color:#777}
  .feature-cta{left:111px;top:2738px;width:142px;height:50px;line-height:50px;text-align:center;font-size:16px}
  .thumb{left:612px;width:205px;height:170px}
  .post-mini{left:845px;width:250px}
  .post-mini h3{font-family:"Montserrat",sans-serif;font-size:16px;font-weight:500;color:#222}
  .post-mini .date{margin-top:8px}
  .post-mini p{margin-top:8px;font-size:12.5px;line-height:25px;color:#777}

  /* faq */
  .faq{top:2871px;left:0;width:1200px;height:636px;background:var(--teal-bright)}
  .faq-title{top:65px;color:#fff}
  .faq-item{left:258px;width:684px;height:54px;border:2px solid rgba(255,255,255,.85);border-radius:27px;color:#fff;font-family:"Montserrat",sans-serif;font-size:16.5px;display:flex;align-items:center;padding-left:20px}
  .faq-item b{font-weight:500;font-size:22px;margin-right:10px}
  .faq-item svg{position:absolute;right:24px;top:18px}
  .faq-answer{left:306px;top:211px;width:600px;color:#fff;font-style:italic;font-size:13px;line-height:28px}

  /* footer */
  .site-footer{top:3507px;left:0;width:1200px;height:396px;background:var(--footer);color:#fff}
  .foot-h{font-size:21px;font-weight:500}
  .field{position:absolute;height:36px;background:#fff;color:#333;font-size:11px;padding:13px 12px 0}
  .submit{left:116px;top:245px;width:98px;height:34px;line-height:34px;text-align:center;font-size:14px}
  .contact-row{left:572px;display:flex;gap:14px;font-size:11.5px;line-height:18px}
  .contact-row .icon{width:42px;height:42px;border:2px solid #fff;border-radius:50%;display:flex;align-items:center;justify-content:center;flex:none}
  .contact-row strong{display:block;font-family:"Montserrat",sans-serif;font-weight:500;font-size:15px}
  .foot-badge{left:847px;top:48px;width:184px;height:184px;border-radius:50%;background:#fff;display:flex;align-items:center;justify-content:center;text-align:center;font-family:"Montserrat",sans-serif;font-weight:600;font-size:18px;line-height:1.25;color:var(--teal)}
  .social{top:262px;width:36px;height:36px;border:2px solid #fff;border-radius:50%}
  .copyright{left:0;top:360px;width:1200px;text-align:center;font-family:"Montserrat",sans-serif;font-size:15px}
</style>
</head>
<body>

<header class="abs site-header">
  <nav class="abs main-nav">
    <span class="active">HOME</span><span>ABOUT</span><span>SERVICES</span><span>FAQS</span><span>BLOG</span><span>CONTACT</span>
  </nav>
</header>
<div class="abs brand-badge">Harborline<br>Families</div>

<section class="abs hero" role="img" aria-label="Portrait of the postpartum doula smiling outdoors in a blue top, soft green garden behind"></section>
<div class="abs hero-kicker heading">HARBORLINE FAMILIES</div>
<h1 class="abs hero-title heading">POSTPARTUM CARE</h1>
<a class="abs btn btn-orange hero-cta">LET’S GET STARTED</a>

<section>
  <h2 class="abs about-title heading">ABOUT US</h2>
  <div class="abs about-sub heading">HARBORLINE FAMILIES POSTPARTUM CARE</div>
  <div class="abs about-copy">
    <p>Hi, I’m Dana Ruiz, a certified postpartum care expert and educator serving families of all varieties in the greater San Diego area and beyond.</p>
    <p>My passion as a professional is showing new parents just like you that whether you’ve just had your first child or your fifth, you can not only survive your postpartum period (also known as the 4th trimester), but you and your family can THRIVE – with the kind of compassionate, skilled, and targeted support for your unique needs that only an expert can provide. That’s where I come in.</p>
  </div>
  <a class="abs btn btn-teal about-cta">READ MORE</a>
  <div class="abs about-photo" role="img" aria-label="Family photo of two parents and a child under a large tree"></div>
</section>

<section class="abs key-areas">
  <div class="abs key-photo" role="img" aria-label="The doula holding two sleeping newborn twins, fading into the orange band"></div>
  <h2 class="abs key-title heading">KEY AREAS</h2>
  <div class="abs key-rule"></div>
  <ul class="abs key-list">
    <li><svg width="14" height="11" viewBox="0 0 14 11"><path d="M1 6l4 4 8-9" fill="none" stroke="#fff" stroke-width="2.4"/></svg>I enhance <b>bonding and attachment</b> between parents(s) and baby in the areas of feeding, soothing, learning baby’s cues, babywearing, and playing with baby.</li>
    <li><svg width="14" height="11" viewBox="0 0 14 11"><path d="M1 6l4 4 8-9" fill="none" stroke="#fff" stroke-width="2.4"/></svg>I provide <b>practical, evidence-based information</b> about baby care and help identify what is normal and what is outside the range of normal for parent(s) and baby.</li>
    <li><svg width="14" height="11" viewBox="0 0 14 11"><path d="M1 6l4 4 8-9" fill="none" stroke="#fff" stroke-width="2.4"/></svg>I prioritize the <b>mental and emotional health</b> of parent(s) and help identify potential warning signs that indicate that medical care may be needed.</li>
    <li><svg width="14" height="11" viewBox="0 0 14 11"><path d="M1 6l4 4 8-9" fill="none" stroke="#fff" stroke-width="2.4"/></svg>I offer <b>hands-on support</b> with baby(ies), older siblings, pets, and light home upkeep and meal preparation.</li>
  </ul>
</section>

<section>
  <h2 class="abs section-title blog-title heading">LATEST <span>BLOG</span></h2>
  <div class="abs title-rule" style="top:2173px;background:var(--teal)"></div>
  <div class="abs feature-photo" role="img" aria-label="The doula with new parents holding their newborn"></div>
  <h3 class="abs feature-heading heading">Sed ut perspiciatis unde omnis iste natus error sit</h3>
  <div class="abs date feature-date">30 Sep 2021</div>
  <p class="abs feature-copy">Nemo enim ipsam voluptatem quia voluptas sit aspernatur aut odit aut fugit, sed quia consequuntur magni dolores eos qui ratione voluptatem sequi nes ciunt.Neque porro quisquam est, qui dolorem ipsum quia</p>
  <a class="abs btn btn-orange feature-cta">READ MORE</a>

  <div class="abs thumb" style="top:2232px;background:linear-gradient(120deg,#7a5a48,#c2a38d)" role="img" aria-label="The doula holding a newborn at home"></div>
  <div class="abs thumb" style="top:2421px;background:linear-gradient(120deg,#6f7f58,#4a3b2f)" role="img" aria-label="Two parents and their child under a tree"></div>
  <div class="abs thumb" style="top:2611px;background:linear-gradient(120deg,#2b2b2b,#bdbdbd)" role="img" aria-label="Black and white photo of parents with their newborn"></div>

  <div class="abs post-mini" style="top:2244px"><h3>Sed ut perspiciatis unde om</h3><div class="date">30 Sep 2021</div><p>Nemo enim ipsam voluptatem quia volu ptas sit aspernatur aut odit aut fugit, sed quia consequuntur magni</p></div>
  <div class="abs post-mini" style="top:2434px"><h3>Sed ut perspiciatis unde om</h3><div class="date">30 Sep 2021</div><p>Nemo enim ipsam voluptatem quia volu ptas sit aspernatur aut odit aut fugit, sed quia consequuntur magni</p></div>
  <div class="abs post-mini" style="top:2623px"><h3>Sed ut perspiciatis unde om</h3><div class="date">30 Sep 2021</div><p>Nemo enim ipsam voluptatem quia volu ptas sit aspernatur aut odit aut fugit, sed quia consequuntur magni</p></div>
</section>

<section class="abs faq">
  <h2 class="abs section-title faq-title heading">OUR FAQ’S</h2>
  <div class="abs title-rule" style="top:111px;background:#fff"></div>
  <div class="abs faq-item" style="top:141px"><b>Q.</b>What is a postpartum care expert (doula)?<svg width="14" height="14" viewBox="0 0 14 14"><circle cx="7" cy="7" r="7" fill="#fff"/><path d="M4 6l3 3 3-3" fill="none" stroke="#1ab89f" stroke-width="2"/></svg></div>
  <p class="abs faq-answer">A postpartum care expert is a professional who provides emotional, informational, and physical support to parents who have recently given birth.A postpartum care expert is a professional who informational, and physical support to parents who have recently given birth.</p>
  <div class="abs faq-item" style="top:333px"><b>Q.</b>Do you provide nanny services?<svg width="14" height="14" viewBox="0 0 14 14"><circle cx="7" cy="7" r="7" fill="#fff"/><path d="M6 4l3 3-3 3" fill="none" stroke="#1ab89f" stroke-width="2"/></svg></div>
  <div class="abs faq-item" style="top:403px"><b>Q.</b>What kinds of medical support can you offer?<svg width="14" height="14" viewBox="0 0 14 14"><circle cx="7" cy="7" r="7" fill="#fff"/><path d="M6 4l3 3-3 3" fill="none" stroke="#1ab89f" stroke-width="2"/></svg></div>
  <div class="abs faq-item" style="top:473px"><b>Q.</b>Are you available for overnight shifts?<svg width="14" height="14" viewBox="0 0 14 14"><circle cx="7" cy="7" r="7" fill="#fff"/><path d="M6 4l3 3-3 3" fill="none" stroke="#1ab89f" stroke-width="2"/></svg></div>
  <div class="abs faq-item" style="top:542px"><b>Q.</b>I had a surgical birth. How can you support me?<svg width="14" height="14" viewBox="0 0 14 14"><circle cx="7" cy="7" r="7" fill="#fff"/><path d="M6 4l3 3-3 3" fill="none" stroke="#1ab89f" stroke-width="2"/></svg></div>
</section>

<footer class="abs site-footer">
  <h3 class="abs foot-h heading" style="left:116px;top:52px">CONTACT US</h3>
  <div class="field" style="left:116px;top:112px;width:182px">First Name :</div>
  <div class="field" style="left:306px;top:112px;width:182px">Last Name :</div>
  <div class="field" style="left:116px;top:156px;width:182px">Company Name :</div>
  <div class="field" style="left:306px;top:156px;width:182px">Email address :</div>
  <div class="field" style="left:116px;top:202px;width:372px">Comment :</div>
  <a class="abs btn btn-orange submit">SUBMIT</a>

  <h3 class="abs foot-h heading" style="left:581px;top:52px">ADDRESS</h3>
  <div class="abs contact-row" style="top:120px"><span class="icon"><svg width="14" height="18" viewBox="0 0 14 18"><path d="M7 17s6-6.5 6-10.5A6 6 0 0 0 1 6.5C1 10.5 7 17 7 17z" fill="none" stroke="#fff" stroke-width="1.6"/><circle cx="7" cy="6.5" r="2" fill="#fff"/></svg></span><div><strong>ADDRESS</strong>#25 Lorem Ipsum Dummy<br>Lorem Ipsum Dummy</div></div>
  <div class="abs contact-row" style="top:194px"><span class="icon"><svg width="16" height="16" viewBox="0 0 16 16"><path d="M3 1l3 3-2 2c1 2 3 4 5 5l2-2 3 3-2 3C7 14 2 9 1 3z" fill="#fff"/></svg></span><div><strong>PHONE</strong>00.121.1231</div></div>
  <div class="abs contact-row" style="top:264px"><span class="icon"><svg width="16" height="12" viewBox="0 0 16 12"><rect x="0" y="0" width="16" height="12" rx="1" fill="#fff"/><path d="M0 1l8 6 8-6" fill="none" stroke="#1d1d1d" stroke-width="1.4"/></svg></span><div><strong>EMAIL</strong>info@companyname.com</div></div>

  <div class="abs foot-badge">Harborline<br>Families</div>
  <span class="abs social" style="left:879px" aria-label="Social profile link"></span>
  <span class="abs social" style="left:922px" aria-label="Social profile link"></span>
  <span class="abs social" style="left:965px" aria-label="Social profile link"></span>

  <div class="abs copyright">©2021 Harborline Families.All rights reserved.</div>
</footer>

</body>
</html>
```